New B2C website design to help dads be better dads

DadHarbor is a website to help dads be the “best dad you can be.”

We require our website to be designed into a PSD format, no coding necessary.

The general concept is a two-page design. The first page is the login page, the second page is the home page. Once at the home page, rather than navigating to and from different pages, the user will push and pull through different visual and functional layers of the hierarchy. In theory, this should add to the user experience by having a visual anchor of where they are (through layered pagination) as well as improving loading times since the new information should only be a delta in data load versus a brand new page load.

The general look-and-feel we are going for is clean, simple, minimal. This means that the winning design will show us a good eye for web-optimized typography, good use of white (negative) space, and good use of a visually pleasing grid.

We require a total of 6 page "views" plus the landing page. We note that many of the views are similar to one another.
Landing page
Milestone view
Task view
Content view, articles
Content view, products
Search view
What's new view

Please review all of the additional information provided as well as the attachments for examples.

We provide the following websites as good references for:

Typography:
http://example-kelvorn.com/journal/

Use of white space:
http://www.trenvaskit.com/
http://moldrefin.com/

Example for “scrolling” page concept as well as good balance of color, typography, and white space:
http://www.qorbitalmeet.eu/

Please contact us with questions so that we can guide your design effort.
Updates

Hello designers,

The following information is added to help guide the design process:

1.  For the text dialogue below the landing page, please assume the following word count:
"why are we making dad harbor?": 250 words
"who are we?" 200 words
"what's the deal with the penguin logo?" 300 words

For the social media links, please see http://www.gravelplumbs.com/
Notice the floating "social" bar that is always to the right.  This is the concept we are going for, please try to implement this as you see fit. 

Target Market(s)

Fathers of young children ages 0-6 years old.

Industry/Entity Type

Product

Font styles to use
Sans Serif

Requirements
Must have
• Clean lines, minimal design concept

Incorporation of our logo (see attached document)

Header content is static for all views after landing page, see example

This page WILL be responsive, please keep that in mind when designing
The timeline bar should be to the left, with the timeline bar’s “milestones” also being responsive.

Designer is free to suggest font types, but any fonts used must be royalty-free and web-optimized. We request a minimum number of font types as well as fonts that load relatively fast. We reinforce that visually appealing typography is a significant factor in the winning design choice.

While we are not expecting the winning design to include code, please keep in mind that the final implementation needs to be optimized for desktop, tablet, and mobile platforms.

If you are using stock photography that is not generated by you, please provide where/how we can obtain imagery, as well as price.

All custom graphics must be available in original formats; Photoshop/GIMP layered files for layout design, and vector formats for logos, icons and other graphical elements.

Please incorporate “Blue” into design elements as you see fit, as the RGB 67 74 169 Blue is the primary color used in our brand. The complement to this blue is 255 202 0, a brownish orange. Feel free to use this color as well, although please keep it to a lesser amount.

Background color is your choice, do not feel the need to use the grey.
Should not have
• Excessive graphical content such that it affects loading times

Excessive use of too many font types such that it affects loading times

```html
<!DOCTYPE html>
<html lang="en">
<head>
<meta charset="utf-8">
<title>DadHarbor — Be the best dad you can be</title>
<link rel="stylesheet" href="https://fonts.googleapis.com/css2?family=Noto+Serif:wght@400&family=Source+Sans+3:wght@300;400;600;700&display=swap">
<style>
  :root {
    --brand-blue: #434aa9;
    --heading-blue: #3d44a3;
    --deep-blue: #2e3192;
    --footer-blue: #2b2f8f;
    --footer-bottom: #25287e;
    --sun: #f4c20d;
    --body-text: #707070;
    --muted: #8a8a8a;
    --grey-band: #f1f1f1;
    --footer-link: #dfe1f5;
    --white: #ffffff;
  }
  * { box-sizing: border-box; margin: 0; padding: 0; }
  html, body { width: 688px; height: 1200px; overflow: hidden; background: var(--white); }
  body { position: relative; font-family: "Source Sans 3", "Helvetica Neue", Arial, sans-serif; color: var(--body-text); }

  /* Header */
  .site-header { position: absolute; left: 0; top: 0; width: 688px; height: 86px; border-bottom: 1px solid #e3e6ef; background: var(--white); }
  .brand { position: absolute; left: 44px; top: 24px; display: flex; align-items: center; gap: 8px; }
  .brand-mark { width: 30px; height: 30px; border-radius: 50%; background: var(--brand-blue); flex: none; }
  .brand-name { font-weight: 700; font-size: 15px; color: var(--brand-blue); letter-spacing: 0.3px; }
  .login { position: absolute; left: 418px; top: 37px; display: flex; gap: 6px; }
  .login-field { width: 83px; height: 17px; border: 1px solid #cfcfcf; border-radius: 2px; font-size: 7.5px; color: #888; padding: 3px 6px; line-height: 10px; }
  .login-button { width: 44px; height: 17px; background: var(--brand-blue); color: var(--white); font-size: 7px; font-weight: 600; border-radius: 2px; text-align: center; line-height: 17px; }
  .login-links { position: absolute; right: 49px; top: 59px; font-size: 6.5px; color: var(--muted); display: flex; gap: 17px; }

  /* Hero */
  .hero { position: absolute; left: 0; top: 87px; width: 688px; height: 295px; overflow: hidden; }
  .hero-photo { position: absolute; inset: 0; background: radial-gradient(ellipse at 72% 45%, #ffffff 0%, #e6eff9 30%, #a3c6ec 68%, #74a9e0 100%); }
  .hero-title { position: absolute; left: 70px; top: 69px; font-family: "Noto Serif", Georgia, serif; font-size: 28px; line-height: 31px; color: var(--deep-blue); letter-spacing: 0.3px; }
  .hero-sub { position: absolute; left: 72px; top: 133px; font-size: 15px; line-height: 16px; color: var(--deep-blue); }
  .hero-copy { position: absolute; left: 72px; top: 169px; width: 216px; font-size: 7.8px; line-height: 13px; color: #4f5b8a; }
  .hero-arrow { position: absolute; top: 127px; width: 30px; height: 30px; border-radius: 50%; background: rgba(255,255,255,0.7); }
  .hero-arrow.prev { left: 20px; }
  .hero-arrow.next { right: 20px; }
  .hero-arrow svg { position: absolute; left: 10px; top: 9px; }
  .hero-cta { position: absolute; left: 234px; top: 352px; width: 202px; height: 30px; background: var(--brand-blue); color: var(--white); font-size: 9.5px; font-weight: 600; letter-spacing: 0.8px; text-align: center; line-height: 30px; }
  .hero-cta-chevron { position: absolute; left: 326px; top: 380px; }

  /* About */
  .about-heading { position: absolute; left: 80px; top: 400px; width: 528px; display: flex; align-items: center; gap: 14px; }
  .about-heading .rule { flex: 1; height: 1px; background: var(--sun); }
  .about-title { font-size: 22px; font-weight: 300; color: var(--sun); white-space: nowrap; }

  .story { position: absolute; left: 0; width: 688px; }
  .story-text { position: absolute; }
  .story-text h2 { font-size: 17.5px; font-weight: 300; color: var(--heading-blue); line-height: 22px; margin-bottom: 6px; }
  .story-text p { font-size: 8.4px; line-height: 13.8px; color: var(--body-text); font-weight: 400; margin-bottom: 7px; }
  .story-photo { position: absolute; width: 134px; height: 134px; border-radius: 50%; border: 4px solid var(--white); box-shadow: 0 0 0 1px #dddddd; }

  .story-why { top: 440px; height: 158px; }
  .story-who { top: 598px; height: 217px; background: var(--grey-band); border-top: 1px solid #e6e6e6; border-bottom: 1px solid #e6e6e6; }
  .story-logo { top: 815px; height: 194px; }

  .photo-garden { background: radial-gradient(circle at 50% 55%, #d9c2ad 0%, #9fb38a 45%, #4f7a3b 100%); }
  .photo-field { background: linear-gradient(180deg, #e9d9b0 0%, #c9b77a 45%, #6f9a3e 70%, #4d7a2a 100%); }

  .logo-display { position: absolute; left: 478px; top: 49px; display: flex; align-items: center; gap: 10px; }
  .logo-display .brand-mark { width: 44px; height: 44px; }
  .logo-display .brand-name { font-size: 19px; }

  /* Footer */
  .site-footer { position: absolute; left: 0; top: 1009px; width: 688px; height: 151px; background: var(--footer-blue); }
  .footer-col { position: absolute; top: 26px; }
  .footer-col h3 { font-size: 13px; font-weight: 400; color: var(--white); margin-bottom: 5px; }
  .footer-col ul { list-style: none; }
  .footer-col li { font-size: 7.8px; line-height: 14.5px; color: var(--footer-link); font-weight: 400; }
  .footer-divider { position: absolute; top: 25px; width: 1px; height: 100px; background: rgba(255,255,255,0.18); }
  .social { display: flex; gap: 4px; margin-top: 4px; }
  .social span { width: 17px; height: 17px; border-radius: 50%; background: var(--white); }
  .footer-bottom { position: absolute; left: 0; top: 1160px; width: 688px; height: 40px; background: var(--footer-bottom); font-size: 7.5px; color: #7a7ec0; padding: 13px 40px; }
</style>
</head>
<body>

<header class="site-header">
  <div class="brand">
    <span class="brand-mark"></span>
    <span class="brand-name">DADHARBOR</span>
  </div>
  <div class="login">
    <div class="login-field">username</div>
    <div class="login-field">password</div>
    <div class="login-button">SIGN IN</div>
  </div>
  <div class="login-links"><span>Forgot login?</span><span>Request access</span></div>
</header>

<section class="hero">
  <div class="hero-photo" role="img" aria-label="Father lifting his young son into a bright blue sky with white clouds"></div>
  <h1 class="hero-title">BE THE BEST DAD<br>YOU CAN BE</h1>
  <p class="hero-sub">The Portal created exclusively<br>for dads, by dads</p>
  <p class="hero-copy">Duis tincidunt lectus quis dui viverra vestibulum. Suspend-isse vulputate aliquam dui. Nulla elementum dui ut augue. Aliquam vehicula mi at mauris.</p>
  <span class="hero-arrow prev"><svg width="10" height="12" viewBox="0 0 10 12"><path d="M7 1 L2 6 L7 11" fill="none" stroke="#5a6a9a" stroke-width="1.4"/></svg></span>
  <span class="hero-arrow next"><svg width="10" height="12" viewBox="0 0 10 12"><path d="M3 1 L8 6 L3 11" fill="none" stroke="#5a6a9a" stroke-width="1.4"/></svg></span>
</section>

<div class="hero-cta">LEARN ABOUT DAD HARBOR</div>
<svg class="hero-cta-chevron" width="20" height="12" viewBox="0 0 20 12"><path d="M0 0 L10 10 L20 0 Z" fill="#434aa9"/><path d="M5 2 L10 7 L15 2" fill="none" stroke="#ffffff" stroke-width="1.6"/></svg>

<div class="about-heading">
  <span class="rule"></span>
  <h2 class="about-title">About Dad Harbor</h2>
  <span class="rule"></span>
</div>

<section class="story story-why">
  <div class="story-text" style="left:36px; top:20px; width:410px;">
    <h2>Why are we making Dad Harbor?</h2>
    <p>Lorem ipsum dolor sit amet, consectetur adipisicing elit, sed do eiusmod tempor incididunt ut labore et dolore magna aliqua. Ut enim ad minim veniam, quis nostrud exercitation ullamco laboris nisi ut aliquip ex ea commodo consequat.</p>
    <p>Duis aute irure dolor in reprehenderit in voluptate velit esse cillum dolore eu fugiat nulla pariatur. Excepteur sint occaecat cupidatat non proident, sunt in culpa qui officia deserunt mollit anim id est laborum</p>
  </div>
  <div class="story-photo photo-garden" style="left:479px; top:7px;" role="img" aria-label="Smiling father carrying his son piggyback outdoors among green trees"></div>
</section>

<section class="story story-who">
  <div class="story-photo photo-field" style="left:55px; top:41px;" role="img" aria-label="Boy riding on his father's shoulders in a sunny grass field, arms spread wide"></div>
  <div class="story-text" style="left:230px; top:53px; width:392px;">
    <h2>Who are we?</h2>
    <p>Lorem ipsum dolor sit amet, consectetur adipisicing elit, sed do eiusmod tempor incididunt ut labore et dolore magna aliqua. Ut enim ad minim veniam, quis nostrud exercitation ullamco laboris nisi ut aliquip ex ea commodo consequat.</p>
    <p>Duis aute irure dolor in reprehenderit in voluptate velit esse cillum dolore eu fugiat nulla pariatur. Excepteur sint occaecat cupidatat non proident, sunt in culpa qui officia deserunt mollit anim id est laborum</p>
  </div>
</section>

<section class="story story-logo">
  <div class="story-text" style="left:36px; top:43px; width:400px;">
    <h2>What's the deal with the Penguin logo?</h2>
    <p>Lorem ipsum dolor sit amet, consectetur adipisicing elit, sed do eiusmod tempor incididunt ut labore et dolore magna aliqua. Ut enim ad minim veniam, quis nostrud exercitation ullamco laboris nisi ut aliquip ex ea commodo consequat.</p>
    <p>Duis aute irure dolor in reprehenderit in voluptate velit esse cillum dolore eu fugiat nulla pariatur. Excepteur sint occaecat cupidatat non proident, sunt in culpa qui officia deserunt mollit anim id est laborum</p>
  </div>
  <div class="logo-display">
    <span class="brand-mark"></span>
    <span class="brand-name">DADHARBOR</span>
  </div>
</section>

<footer class="site-footer">
  <div class="footer-col" style="left:50px;">
    <h3>Company</h3>
    <ul><li>Cum sociis</li><li>Natoque penatibus</li><li>Magnis dis parturient</li><li>Montes nascetur</li><li>Ridiculus mus</li></ul>
  </div>
  <span class="footer-divider" style="left:139px;"></span>
  <div class="footer-col" style="left:162px;">
    <h3>Services</h3>
    <ul><li>Services Provide</li><li>Natoque penatibus</li><li>Montes nascetur</li><li>Ridiculus mus</li></ul>
  </div>
  <span class="footer-divider" style="left:257px;"></span>
  <div class="footer-col" style="left:275px;">
    <h3>Support</h3>
    <ul><li>Customer Service</li><li>Legal</li><li>Sitemap</li><li>Resources</li></ul>
  </div>
  <span class="footer-divider" style="left:353px;"></span>
  <div class="footer-col" style="left:375px;">
    <h3>Sublinks</h3>
    <ul><li>Services Provide</li><li>Natoque penatibus</li><li>Montes nascetur</li><li>Ridiculus mus</li></ul>
  </div>
  <span class="footer-divider" style="left:467px;"></span>
  <div class="footer-col" style="left:491px;">
    <h3>Get Connected</h3>
    <div class="social"><span></span><span></span><span></span><span></span></div>
  </div>
</footer>
<div class="footer-bottom">© 2013 Company Name.&nbsp; All right reserved.&nbsp; Term of Use</div>

</body>
</html>
```